Business Card for Polygraph business in Africa

Business Card . Polygraph Examiner based in Tanzania, East Africa.
Business Card will be used to disseminate contact information to potential clients.
It should convey that I am a professional specifically in the polygraph field and perform my work with integrity.

I have attached the business card that I'm currently using, which I threw together myself initially. It's not professional enough.

Target Market(s)

Banks, Accounting Firms, Government Ministries, Gas, Oil, & Gemstone Mining Concerns, Wildlife Conservation NGOs, International companies located in East Africa.

Industry/Entity Type

Business

Contact Information for Business Card

Veritrace Kilonga
Miriam Holloway
PO Box 48317
Arusha, Tanzania
+255 612 839 274
miriamholloway@postvale.example

Colors
00a990
f37122
faa54b

Requirements
Must have
• - Veritrace Kilonga (with the word "Polygraph" being more prominent than the word "Tanzania")
• - Forensic Examinations
• - Employment Screening
• - Should contain a logo of the Continental Truthline Society (of which I'm a member)
• - I would like an accent design (such as the polygraph "squiggles" of a cardio tracing or such as that)
• - My contact information (less prominent, but large enough to read legibly). I would also consider putting the contact information on the second side of the card.
Nice to have
• My color suggestions are changeable.
Should not have
• Anything "cutesy" or "cartoonish"

```html
<!DOCTYPE html>
<html lang="en">
<head>
<meta charset="utf-8">
<title>Veritrace Kilonga – Business Card</title>
<link href="https://fonts.googleapis.com/css2?family=Oswald:wght@400;500&family=Open+Sans:wght@400&display=swap" rel="stylesheet">
<style>
  :root {
    --stage: #161616;
    --teal: #00a990;
    --orange: #f37122;
    --ink: #2b2b2b;
    --paper: #ffffff;
    --seal-ring: #2a2a5e;
  }
  html, body {
    margin: 0;
    width: 1200px;
    height: 900px;
    overflow: hidden;
    background: var(--stage);
  }
  .stage { position: relative; width: 1200px; height: 900px; }
  .card { position: absolute; top: 306px; width: 440px; height: 272px; overflow: hidden; }

  /* Front */
  .card-front { left: 149px; background: var(--paper); }
  .tag { position: absolute; left: 0; top: 26px; }
  .holder { position: absolute; left: 39px; top: 29px; font-family: "Oswald", sans-serif; }
  .holder-name { margin: 0; font-size: 14px; font-weight: 500; letter-spacing: .3px; line-height: 16px; }
  .holder-name .first { color: var(--teal); }
  .holder-name .last { color: var(--orange); }
  .holder-role { margin: 0; font-family: "Open Sans", sans-serif; font-size: 11.5px; color: var(--ink); line-height: 14px; }
  .brand-front {
    position: absolute; left: 233px; top: 104px;
    font-family: "Oswald", sans-serif; font-weight: 400; font-size: 21px;
    color: var(--teal); margin: 0; letter-spacing: .2px;
  }
  .contact {
    position: absolute; left: 24px; top: 167px;
    font-family: "Open Sans", sans-serif; font-size: 11.5px; color: var(--ink); line-height: 16px;
  }
  .contact address { font-style: normal; margin-bottom: 8px; }
  .contact-line { display: flex; align-items: center; gap: 5px; }
  .services {
    position: absolute; right: 28px; top: 211px; margin: 0; padding: 0; list-style: none;
    font-family: "Open Sans", sans-serif; font-size: 11.5px; color: var(--ink); line-height: 16px; text-align: right;
  }
  .services li::after { content: " •"; color: var(--orange); }
  .footer-bands { position: absolute; left: 0; bottom: 0; }

  /* Back */
  .card-back {
    left: 608px;
    background: linear-gradient(140deg, var(--orange) 0%, #c98a3f 18%, var(--teal) 48%, #5b9c78 68%, var(--orange) 90%);
  }
  .brand-back {
    position: absolute; left: 0; right: 0; top: 86px; margin: 0; text-align: center;
    font-family: "Oswald", sans-serif; font-weight: 400; font-size: 22px; color: var(--paper);
  }
  .seal {
    position: absolute; left: 166px; top: 136px; width: 110px; height: 110px;
    border-radius: 50%; background: var(--paper); box-sizing: border-box;
    border: 5px solid var(--seal-ring);
  }
</style>
</head>
<body>
<main class="stage">
  <section class="card card-front" aria-label="Card front">
    <svg class="tag" width="30" height="38" viewBox="0 0 30 38" aria-hidden="true">
      <polygon points="0,0 13,0 16,38 0,38" fill="var(--teal)"/>
      <polygon points="13,0 28,0 28,38 16,38" fill="var(--orange)"/>
    </svg>
    <div class="holder">
      <h2 class="holder-name"><span class="first">MIRIAM</span> <span class="last">HOLLOWAY</span></h2>
      <p class="holder-role">Owner</p>
    </div>
    <h1 class="brand-front">Veritrace Kilonga</h1>
    <div class="contact">
      <address>PO Box 48317<br>Arusha, Tanzania</address>
      <div class="contact-line">
        <svg width="10" height="10" viewBox="0 0 24 24" aria-hidden="true"><path fill="var(--teal)" d="M6.6 10.8a15.2 15.2 0 0 0 6.6 6.6l2.2-2.2a1 1 0 0 1 1-.25 11.4 11.4 0 0 0 3.6.57 1 1 0 0 1 1 1V20a1 1 0 0 1-1 1A17 17 0 0 1 3 4a1 1 0 0 1 1-1h3.5a1 1 0 0 1 1 1c0 1.25.2 2.45.57 3.57a1 1 0 0 1-.25 1z"/></svg>
        <span>+255 612 839 274</span>
      </div>
      <div class="contact-line">
        <svg width="10" height="8" viewBox="0 0 20 14" aria-hidden="true"><rect width="20" height="14" rx="1" fill="var(--teal)"/><path d="M1 1l9 7 9-7" stroke="#fff" stroke-width="1.6" fill="none"/></svg>
        <span>miriamholloway@postvale.example</span>
      </div>
    </div>
    <ul class="services">
      <li>Forensic Examinations</li>
      <li>Employment Screening</li>
    </ul>
    <svg class="footer-bands" width="440" height="20" viewBox="0 0 440 20" aria-hidden="true">
      <polygon points="0,6 218,6 210,20 0,20" fill="var(--teal)"/>
      <polygon points="224,0 440,0 440,20 207,20" fill="var(--orange)"/>
    </svg>
  </section>

  <section class="card card-back" aria-label="Card back">
    <h1 class="brand-back">Veritrace Kilonga</h1>
    <div class="seal" role="img" aria-label="Continental Truthline Society membership seal"></div>
  </section>
</main>
</body>
</html>
```